Modern Verdell Tree Care Website

I need a website for a full service Tree Care company. The company provides tree pruning, tree removal, tree preservation, emergency services, stump grinding, and emergency tree services.

Target Market(s)

Customers that need tree services

Industry/Entity Type

Landscaping, Tree Services

Coding

Coded - Design and coding required

Number of Pages Required

5+ page

Font styles to use
Sans Serif

Requirements
Must have
• Good clean design that showcases the services the company provides.
Nice to have
• Services page; contact form, blog, home page, about page

```html
<!DOCTYPE html>
<html lang="en">
<head>
<meta charset="utf-8">
<title>Verdell Tree Care</title>
<link href="https://fonts.googleapis.com/css2?family=Russo+One&family=Inter:wght@400;500;600&family=Rajdhani:wght@600;700&display=swap" rel="stylesheet">
<style>
:root{
  --green:#7bc143;
  --green-dark:#5f9e2f;
  --orange:#f2a33a;
  --ink:#3a3d38;
  --text:#4b4e49;
  --muted:#7b7e78;
  --cream:#f6f4ef;
  --footer:#1a1d17;
  --line:#b9bbb5;
}
*{box-sizing:border-box;margin:0;padding:0}
html,body{width:1200px;height:4389px;overflow:hidden}
body{position:relative;background:#fff;font-family:'Inter',sans-serif;color:var(--text)}
.abs{position:absolute}
.display{font-family:'Russo One',sans-serif;color:var(--ink);font-weight:400}
.photo{position:absolute;border-radius:14px;overflow:hidden}
.btn{position:absolute;display:flex;align-items:center;justify-content:center;gap:6px;background:var(--green);color:#fff;font-family:'Rajdhani',sans-serif;font-weight:700;letter-spacing:2px;font-size:13px;text-transform:uppercase}
.brand{font-family:'Russo One',sans-serif;color:var(--ink);display:flex;align-items:center;gap:12px}
.brand-mark{width:40px;height:40px;background:var(--green)}

/* hero */
.hero{position:absolute;left:0;top:0;width:1200px;height:658px;background:radial-gradient(ellipse at 45% 10%,#fbeedd 0,rgba(251,238,221,0) 45%),radial-gradient(ellipse at 0% 70%,#e6f0d8 0,rgba(230,240,216,0) 45%),radial-gradient(ellipse at 100% 20%,#e4efd4 0,rgba(228,239,212,0) 35%),var(--cream)}
.nav{position:absolute;top:40px;display:flex;gap:48px;left:630px;font-size:13px;color:var(--ink)}
.nav .active{color:var(--orange)}
.hero h1{position:absolute;left:85px;top:200px;font-size:55px;line-height:65px;width:520px}
.hero-sub{position:absolute;left:85px;top:413px;font-size:18px;font-weight:500;color:var(--ink)}

/* sections */
.services-band{position:absolute;left:0;top:1316px;width:1200px;height:658px;background:radial-gradient(ellipse at 100% 5%,#e3eed3 0,rgba(227,238,211,0) 40%),radial-gradient(ellipse at 60% 90%,#fbecd9 0,rgba(251,236,217,0) 40%),var(--cream)}
.contact-band{position:absolute;left:0;top:2632px;width:1200px;height:658px;background:radial-gradient(ellipse at 0% 10%,#e6f0d8 0,rgba(230,240,216,0) 40%),radial-gradient(ellipse at 90% 60%,#fbecd9 0,rgba(251,236,217,0) 40%),var(--cream)}
h2.display{position:absolute;font-size:44px;line-height:52px}
.para{position:absolute;font-size:14px;line-height:22px;color:var(--text)}

.svc-card{position:absolute;top:1474px;width:246px;height:328px;border-radius:8px;overflow:hidden}
.svc-card .cap{position:absolute;left:18px;bottom:26px;font-family:'Russo One',sans-serif;color:#fff;font-size:17px;line-height:22px}
.svc-card .go{position:absolute;right:14px;bottom:22px;width:30px;height:30px;background:var(--green);display:flex;align-items:center;justify-content:center}

.tick-item{position:absolute;display:flex;align-items:center;gap:9px;font-size:14.5px;color:var(--ink)}

.field{position:absolute;border-bottom:1px solid var(--line);font-size:14px;color:var(--text);padding-bottom:14px}

.blog-card{position:absolute;top:3474px;width:322px;height:406px;background:#fff;border-radius:12px;box-shadow:0 4px 18px rgba(0,0,0,.10);overflow:hidden}
.blog-card .img{height:211px}
.blog-card .date{position:absolute;left:14px;top:16px;background:var(--orange);color:#fff;font-size:10.5px;padding:3px 11px;border-radius:10px}
.blog-card h3{font-family:'Russo One',sans-serif;font-weight:400;font-size:17px;line-height:24px;color:var(--ink);margin:22px 28px 0}
.blog-card p{font-size:13.5px;line-height:22px;color:var(--text);margin:12px 28px 0}
.blog-card .more{display:inline-block;margin:10px 28px 0;color:var(--green);font-family:'Rajdhani',sans-serif;font-weight:700;letter-spacing:2px;font-size:13px;border-bottom:1px solid var(--green)}

/* footer */
.footer{position:absolute;left:0;top:3948px;width:1200px;height:441px;background:var(--footer);color:#d8dad4}
.footer h4{position:absolute;font-family:'Russo One',sans-serif;font-weight:400;font-size:16px;color:#fff;padding-bottom:12px}
.footer h4::after{content:"";position:absolute;left:0;bottom:0;width:42px;height:2px;background:var(--orange)}
.footer .list{position:absolute;left:544px;top:154px;list-style:none;font-size:14px;line-height:32.5px}
.footer .small{position:absolute;font-size:14px;line-height:24px}
</style>
</head>
<body>

<!-- HERO -->
<section class="hero">
  <div class="brand abs" style="left:85px;top:24px;font-size:26px">
    <span class="brand-mark"></span><span>Verdell Tree Care</span>
  </div>
  <nav class="nav"><span class="active">Home</span><span>About</span><span>Services</span><span>Blog</span></nav>
  <div class="btn" style="left:975px;top:31px;width:140px;height:39px">Contact
    <svg width="12" height="10" viewBox="0 0 12 10"><path d="M0 5h10M6 1l4 4-4 4" stroke="#fff" stroke-width="1.6" fill="none"/></svg></div>
  <h1 class="display">Call VERDELL for All Your Tree Care Needs</h1>
  <p class="hero-sub">Serving Lafayette and surrounding areas</p>
  <div class="btn" style="left:85px;top:465px;width:176px;height:40px">Discover more
    <svg width="10" height="10" viewBox="0 0 10 10"><path d="M1 9L9 1M3 1h6v6" stroke="#fff" stroke-width="1.5" fill="none"/></svg></div>
  <div class="photo" role="img" aria-label="Arborist trimming a tall hedge with a powered hedge trimmer" style="left:614px;top:114px;width:283px;height:459px;border-radius:0;background:linear-gradient(120deg,#3f7a2a,#7aa84f 45%,#dfe3e0 60%,#3b3e3a)"></div>
  <div class="photo" role="img" aria-label="Worker pruning bare tree branches with shears" style="left:903px;top:114px;width:212px;height:225px;border-radius:0;background:linear-gradient(160deg,#dfe2dc,#b9bdb2 50%,#5d6a3e)"></div>
  <div class="photo" role="img" aria-label="Cutting a log with a chainsaw on grass" style="left:903px;top:348px;width:212px;height:225px;border-radius:0;background:linear-gradient(140deg,#3f7b2c,#5d9a3c 50%,#b58a52)"></div>
  <svg class="abs" style="left:583px;top:600px" width="34" height="50" viewBox="0 0 34 50"><rect x="1" y="1" width="32" height="48" rx="16" fill="none" stroke="var(--green)" stroke-width="2"/><path d="M17 12v24M11 30l6 6 6-6" stroke="var(--green)" stroke-width="2" fill="none"/></svg>
</section>

<!-- WHO WE ARE -->
<div class="photo" role="img" aria-label="Smiling worker in ear defenders holding a hedge trimmer among greenery" style="left:85px;top:779px;width:368px;height:368px;background:linear-gradient(135deg,#a6cf4e,#6da53a 45%,#e6e9e4 75%,#8fb463)"></div>
<div class="photo" role="img" aria-label="Hand holding pruning shears near a green leaf" style="left:361px;top:1007px;width:176px;height:178px;border:5px solid #fff;background:linear-gradient(150deg,#3d6e2b,#7aa045 60%,#e3c34a)"></div>
<h2 class="display" style="left:612px;top:797px">Who we are</h2>
<p class="para" style="left:612px;top:864px;width:503px">At Verdell Tree Care, we are more than just a tree service company, we are stewards of our beautiful trees. With a passion deeply rooted in arboriculture, we embark on a mission to promote the health, beauty, and safety of your trees and landscapes.</p>
<p class="para" style="left:612px;top:962px;width:503px">Whether it's expert tree trimming to enhance aesthetics, meticulous tree removal to mitigate hazards, or comprehensive tree health assessments to ensure safety, we approach each task with unwavering dedication and attention to detail.</p>
<div class="btn" style="left:612px;top:1079px;width:158px;height:41px">Read more
  <svg width="10" height="10" viewBox="0 0 10 10"><path d="M1 9L9 1M3 1h6v6" stroke="#fff" stroke-width="1.5" fill="none"/></svg></div>

<!-- SERVICES -->
<section class="services-band"></section>
<span class="abs" style="left:584px;top:1366px;width:32px;height:32px;background:var(--orange)"></span>
<h2 class="display" style="left:0;top:1401px;width:1200px;text-align:center;font-size:48px">Service We Provide</h2>
<div class="svc-card" role="img" aria-label="Gloved hands pruning a branch with shears" style="left:85px;background:linear-gradient(160deg,#b8c7a5,#6c8f4a 50%,#2b3424)">
  <span class="cap">Tree pruning</span><span class="go"><svg width="10" height="10" viewBox="0 0 10 10"><path d="M1 9L9 1M3 1h6v6" stroke="#fff" stroke-width="1.5" fill="none"/></svg></span></div>
<div class="svc-card" role="img" aria-label="Chainsaw cutting through a tree trunk" style="left:346px;background:linear-gradient(160deg,#4c7a2c,#a48759 55%,#2a2f22)">
  <span class="cap">Tree Removal</span><span class="go"><svg width="10" height="10" viewBox="0 0 10 10"><path d="M1 9L9 1M3 1h6v6" stroke="#fff" stroke-width="1.5" fill="none"/></svg></span></div>
<div class="svc-card" role="img" aria-label="Hand watering a young seedling in soil" style="left:607px;background:linear-gradient(160deg,#c9cbb9,#7e8f5a 50%,#3c3325)">
  <span class="cap">Tree Preservation</span><span class="go"><svg width="10" height="10" viewBox="0 0 10 10"><path d="M1 9L9 1M3 1h6v6" stroke="#fff" stroke-width="1.5" fill="none"/></svg></span></div>
<div class="svc-card" role="img" aria-label="Arborist on a ladder among bare branches" style="left:869px;background:linear-gradient(160deg,#cfd8e2,#8a8f86 55%,#3a3a32)">
  <span class="cap">Emergency<br>services</span><span class="go"><svg width="10" height="10" viewBox="0 0 10 10"><path d="M1 9L9 1M3 1h6v6" stroke="#fff" stroke-width="1.5" fill="none"/></svg></span></div>
<div class="abs" style="left:494px;top:1836px;width:212px;height:41px;border:1.5px solid var(--ink);display:flex;align-items:center;justify-content:center;gap:6px;font-family:'Rajdhani',sans-serif;font-weight:700;letter-spacing:2px;font-size:13px;color:var(--ink)">VIEW ALL SERVICES
  <svg width="12" height="10" viewBox="0 0 12 10"><path d="M0 5h10M6 1l4 4-4 4" stroke="var(--ink)" stroke-width="1.6" fill="none"/></svg></div>

<!-- WHY CHOOSE US -->
<h2 class="display" style="left:85px;top:2153px;font-size:46px">Why Choose Us?</h2>
<svg width="0" height="0" style="position:absolute"><defs><symbol id="tick" viewBox="0 0 20 20"><circle cx="10" cy="10" r="9" fill="#d7e9c1"/><path d="M5 10l4 4 8-10" stroke="var(--green)" stroke-width="2.6" fill="none" stroke-linecap="round"/></symbol></defs></svg>
<div class="tick-item" style="left:85px;top:2236px"><svg width="20" height="20"><use href="#tick"/></svg>Licensed and Insured</div>
<div class="tick-item" style="left:85px;top:2276px"><svg width="20" height="20"><use href="#tick"/></svg>24-Hours Emergency Services</div>
<div class="tick-item" style="left:85px;top:2315px"><svg width="20" height="20"><use href="#tick"/></svg>Locally Owned &amp; Operated</div>
<div class="tick-item" style="left:85px;top:2355px"><svg width="20" height="20"><use href="#tick"/></svg>Professional Work</div>
<div class="tick-item" style="left:356px;top:2236px"><svg width="20" height="20"><use href="#tick"/></svg>Safety is Our No.1 Priority</div>
<div class="tick-item" style="left:356px;top:2276px"><svg width="20" height="20"><use href="#tick"/></svg>Free Estimates</div>
<div class="tick-item" style="left:356px;top:2315px"><svg width="20" height="20"><use href="#tick"/></svg>Licensed Arborist on Staff</div>
<div class="photo" role="img" aria-label="Worker using a pole saw on a tall tree in a forest" style="left:622px;top:2112px;width:237px;height:366px;background:linear-gradient(170deg,#8aa35a,#4f7a31 50%,#2e4a22)"></div>
<div class="photo" role="img" aria-label="Gloved hand cutting a branch against blue sky" style="left:876px;top:2149px;width:239px;height:367px;background:linear-gradient(170deg,#4f86c4,#a9c5e0 45%,#6b7a4f 75%,#d6d8d4)"></div>

<!-- CONTACT -->
<section class="contact-band"></section>
<div class="photo" role="img" aria-label="Smiling worker with ear defenders holding a pole pruner" style="left:89px;top:2756px;width:470px;height:440px;background:linear-gradient(135deg,#2f5a24,#4d7f33 45%,#e9eae6 60%,#c8552f 85%,#2f3a28)"></div>
<h2 class="display" style="left:612px;top:2771px">Get In Touch</h2>
<div class="field" style="left:612px;top:2860px;width:242px">First Name</div>
<div class="field" style="left:871px;top:2860px;width:244px">Last Name</div>
<div class="field" style="left:612px;top:2925px;width:242px">Email</div>
<div class="field" style="left:871px;top:2925px;width:244px">Phone</div>
<div class="field" style="left:612px;top:2990px;width:503px;height:105px">Message</div>
<div class="btn" style="left:612px;top:3124px;width:146px;height:39px">Submit
  <svg width="10" height="10" viewBox="0 0 10 10"><path d="M1 9L9 1M3 1h6v6" stroke="#fff" stroke-width="1.5" fill="none"/></svg></div>

<!-- BLOG -->
<h2 class="display" style="left:0;top:3360px;width:1200px;text-align:center;font-size:48px">Our Latest Blog</h2>
<p class="abs" style="left:0;top:3421px;width:1200px;text-align:center;font-size:16px;color:var(--ink)">Lorem ipsum dolor sit amet, consectetur adipiscing elit.</p>

<article class="blog-card" style="left:85px">
  <div class="img" role="img" aria-label="Gardener shaping a bonsai-like shrub" style="background:linear-gradient(140deg,#5f8f3a,#aebf86 50%,#d8b98a)"></div>
  <span class="date">May 12, 2024</span>
  <h3>Praesent in elit risus vitae magna a dolor</h3>
  <p>Lorem ipsum dolor sit amet, consectetur adipiscing elit. Cras ante nisl, tincidunt non risus at, porttitor volutpat lacus.</p>
  <span class="more">LEARN MORE ↗</span>
</article>
<article class="blog-card" style="left:440px">
  <div class="img" role="img" aria-label="Worker cutting a log with a chainsaw" style="background:linear-gradient(140deg,#5d6350,#9c8b6c 50%,#3d3a30)"></div>
  <span class="date">May 12, 2024</span>
  <h3>Praesent in elit risus vitae magna a dolor</h3>
  <p>Lorem ipsum dolor sit amet, consectetur adipiscing elit. Cras ante nisl, tincidunt non risus at, porttitor volutpat lacus.</p>
  <span class="more">LEARN MORE ↗</span>
</article>
<article class="blog-card" style="left:793px">
  <div class="img" role="img" aria-label="Pruning shears trimming a leafy shrub" style="background:linear-gradient(140deg,#a07a3e,#6f7d3a 50%,#c9b4a0)"></div>
  <span class="date">May 12, 2024</span>
  <h3>Praesent in elit risus vitae magna a dolor</h3>
  <p>Lorem ipsum dolor sit amet, consectetur adipiscing elit. Cras ante nisl, tincidunt non risus at, porttitor volutpat lacus.</p>
  <span class="more">LEARN MORE ↗</span>
</article>

<!-- FOOTER -->
<footer class="footer">
  <div class="brand abs" style="left:85px;top:80px;font-size:27px;color:#fff">
    <span class="brand-mark"></span><span>Verdell Tree Care</span>
  </div>
  <p class="small" style="left:85px;top:164px;width:300px">Call us today to see how we can help you with all of your tree needs:</p>
  <div class="small" style="left:85px;top:224px;font-size:18px;display:flex;gap:10px;align-items:center">
    <svg width="18" height="18" viewBox="0 0 24 24"><path d="M6.6 10.8a15 15 0 006.6 6.6l2.2-2.2a1 1 0 011-.25 11.4 11.4 0 003.6.57 1 1 0 011 1V20a1 1 0 01-1 1A17 17 0 013 4a1 1 0 011-1h3.5a1 1 0 011 1c0 1.25.2 2.45.57 3.57a1 1 0 01-.25 1z" fill="var(--orange)"/></svg>(555) 214-3870</div>
  <div class="small" style="left:85px;top:258px;font-size:18px;display:flex;gap:10px;align-items:center">
    <svg width="18" height="18" viewBox="0 0 24 24"><path d="M6.6 10.8a15 15 0 006.6 6.6l2.2-2.2a1 1 0 011-.25 11.4 11.4 0 003.6.57 1 1 0 011 1V20a1 1 0 01-1 1A17 17 0 013 4a1 1 0 011-1h3.5a1 1 0 011 1c0 1.25.2 2.45.57 3.57a1 1 0 01-.25 1z" fill="var(--orange)"/></svg>(555) 630-4418</div>
  <p class="small" style="left:85px;top:308px">Call HOLLOWAY for a Free Estimate</p>

  <h4 style="left:544px;top:92px">Our Services</h4>
  <ul class="list"><li>Trimming tree</li><li>Removal tree</li><li>Clearing tree</li><li>Pruning stump</li><li>Grinding tree</li></ul>

  <h4 style="left:835px;top:92px">Subscribe Newsletter</h4>
  <p class="small" style="left:835px;top:150px;width:280px">Subscribe us &amp; recieve our offers and update in your inbox directly</p>
  <div class="abs" style="left:835px;top:225px;width:280px;height:39px;background:#fff;border-radius:3px;display:flex;align-items:center;gap:8px;padding-left:12px;font-size:12px;color:#999">
    <svg width="13" height="10" viewBox="0 0 13 10"><rect x=".5" y=".5" width="12" height="9" fill="none" stroke="#aaa"/><path d="M.5 .5l6 5 6-5" stroke="#aaa" fill="none"/></svg>Email address</div>
  <div class="btn" style="left:835px;top:278px;width:280px;height:39px;border-radius:3px">Subscribe
    <svg width="10" height="10" viewBox="0 0 10 10"><path d="M1 9L9 1M3 1h6v6" stroke="#fff" stroke-width="1.5" fill="none"/></svg></div>

  <div class="abs" style="left:85px;top:373px;width:1030px;border-top:1px dashed #6b6e66"></div>
  <p class="abs" style="left:85px;top:398px;font-size:12px">© 2024 <span style="color:var(--green)">Verdell Tree Care</span>. All right reserved</p>
  <p class="abs" style="right:85px;top:398px;font-size:12px">June 12, 2024. Layout_4</p>
</footer>

</body>
</html>
```